Walk Beside The River

Business Card design

Target Market(s)

People who require support in the commnity

Industry/Entity Type

Mental Health Support

Contact Information for Business Card

Mental Health Support Rosalind Tavener walkbesidetheriver@mailcove.com.au 0481 637 092 PO Box 926 Brindlecove QLD 4590

Colors
6B429C
8869AF
B7A5CE
E3DAEB
F3F0F8

Requirements
Must have
• Logo & details listed above
Should not have
• No red or orange

```html
<!DOCTYPE html>
<html lang="en">
<head>
<meta charset="utf-8">
<title>Walk Beside The River – Business Card</title>
<link href="https://fonts.googleapis.com/css2?family=Open+Sans:wght@400;600&display=swap" rel="stylesheet">
<style>
  :root {
    --page: #2a292e;
    --card: #1f1d24;
    --card-edge: #f2e52b;
    --purple: #6b429c;
    --yellow: #f2e52b;
    --text: #ffffff;
    --muted: #2c2933;
  }
  * { box-sizing: border-box; margin: 0; padding: 0; }
  html, body {
    width: 1200px; height: 780px; overflow: hidden;
    background: var(--page);
    font-family: "Open Sans", Arial, sans-serif;
  }
  .stage {
    width: 1200px; height: 780px;
    display: flex; align-items: center; justify-content: center; gap: 36px;
  }
  .card {
    position: relative;
    width: 560px; height: 320px;
    background: var(--card);
    border-radius: 22px;
    border-bottom: 4px solid var(--card-edge);
    box-shadow: 0 18px 40px rgba(0,0,0,.45);
    overflow: hidden;
  }
  .card-back {
    display: flex; align-items: center; justify-content: center;
  }
  .back-name {
    font-size: 30px; font-weight: 600; color: var(--muted);
    letter-spacing: .5px;
  }
  .brand {
    position: absolute; left: 34px; top: 36px;
  }
  .brand-name {
    font-size: 20px; font-weight: 600; color: var(--purple);
  }
  .details {
    position: absolute; left: 34px; top: 112px;
    color: var(--text);
  }
  .role, .person { font-size: 17px; line-height: 24px; }
  .contact-list { list-style: none; margin-top: 8px; }
  .contact-list li {
    display: flex; align-items: center; gap: 10px;
    font-size: 15px; line-height: 24px;
  }
  .contact-list svg { width: 14px; height: 14px; flex: none; }
  .bands {
    position: absolute; left: 0; bottom: 0; width: 560px; height: 80px;
  }
</style>
</head>
<body>
<main class="stage">
  <section class="card card-back" aria-label="Card back">
    <span class="back-name">Walk Beside The River</span>
  </section>

  <section class="card card-front" aria-label="Card front">
    <div class="brand">
      <span class="brand-name">Walk Beside The River</span>
    </div>

    <div class="details">
      <p class="role">Mental Health Support</p>
      <p class="person">Rosalind Tavener</p>
      <ul class="contact-list">
        <li>
          <svg viewBox="0 0 24 24" aria-hidden="true"><path fill="#f2e52b" d="M6.6 10.8a15 15 0 0 0 6.6 6.6l2.2-2.2c.3-.3.7-.4 1-.2 1.1.4 2.3.6 3.6.6.6 0 1 .4 1 1V20c0 .6-.4 1-1 1A17 17 0 0 1 3 4c0-.6.4-1 1-1h3.5c.6 0 1 .4 1 1 0 1.3.2 2.5.6 3.6.1.3 0 .7-.2 1z"/></svg>
          <span>0481 637 092</span>
        </li>
        <li>
          <svg viewBox="0 0 24 24" aria-hidden="true"><path fill="#f2e52b" d="M3 5h18v14H3zm2 2v.5l7 4.5 7-4.5V7zm0 2.8V17h14V9.8l-7 4.5z"/></svg>
          <span>walkbesidetheriver@mailcove.com.au</span>
        </li>
        <li>
          <svg viewBox="0 0 24 24" aria-hidden="true"><path fill="#f2e52b" d="M12 2a7 7 0 0 0-7 7c0 5 7 13 7 13s7-8 7-13a7 7 0 0 0-7-7zm0 9.5A2.5 2.5 0 1 1 12 6.5a2.5 2.5 0 0 1 0 5z"/></svg>
          <span>PO Box 926 Brindlecove QLD 4590</span>
        </li>
      </ul>
    </div>

    <svg class="bands" viewBox="0 0 560 80" aria-hidden="true">
      <polygon points="0,52 330,52 308,74 0,74" fill="var(--yellow)"/>
      <polygon points="350,26 560,26 560,46 330,46" fill="var(--purple)"/>
    </svg>
  </section>
</main>
</body>
</html>
```